BrivoTerna. Lantern of the Steady Harvest. Business card

Professional business card for BrivoTerna (Lantern of the Steady Harvest)
My rationale: Strategy-> Execution-> Results-> Value that lead to the BrivoTerna name: We put the Lantern of the Steady Harvest.
We deliver value to our customers helping them at defining a good strategy (cyan arrow). 90% of well formulated strategies fail due to poor execution so we also consider strategical execution very important (green arrow). Due to the execution we obtain the results (blue arrow). Finally, the results provide feedback to redefine strategy, and the new strategy has to be executed and new results obtained providing new feedback and on and on. It's like a wheel that finally, must create corporate value: value for shareholders, staholders, employees, providers...-

Target Market(s)

CEOs and steering comitees , invewrnent funds

Industry/Entity Type

Business Consultant

Contact Information for Business Card

Teodoro Vinsquel
CEO & Founder
teodoro.vinsquel@brivoterna-example.com
Mobile: +34 655.803.912
www.brivoterna-example.com

Colors

Designer to choose colors to be used in the design.

Requirements
Nice to have
• Nice to hace the words: Strategy, execution, results
• Nice to vave the claim: Lantern of the Steady Harvest
• The three colors should be shown:
• cyan for STRATEGY
• green for EXECUTION
• blue for RESULTS
Should not have
• Complete black background

```html
<!DOCTYPE html>
<html lang="en">
<head>
<meta charset="utf-8">
<title>BrivoTerna – Business Card</title>
<link rel="stylesheet" href="https://fonts.googleapis.com/css2?family=Lato:wght@400;700;900&display=swap">
<style>
  :root {
    --navy: #28318a;
    --green: #8cc63e;
    --cyan: #29a8df;
    --paper: #f6f5ef;
    --cream: #f3f1e6;
    --ink: #3a3a3a;
    --stage: #d8d8d8;
  }
  * { box-sizing: border-box; margin: 0; padding: 0; }
  html, body {
    width: 1200px; height: 787px; overflow: hidden;
    background: var(--stage);
    font-family: 'Lato', sans-serif;
  }
  .sheet {
    width: 1200px; height: 787px;
    display: flex; align-items: center; justify-content: center; gap: 40px;
  }
  .card {
    position: relative;
    width: 540px; height: 309px;
    overflow: hidden;
    box-shadow: 0 6px 16px rgba(0,0,0,0.18);
  }
  /* Front */
  .card--front { background: var(--paper); }
  .brand {
    position: absolute; left: 38px; top: 70px;
    display: flex; align-items: center; gap: 10px;
  }
  .brand__name {
    font-weight: 900; font-size: 44px; letter-spacing: -1px;
    color: var(--navy); line-height: 1;
  }
  .brand__dot {
    width: 16px; height: 16px; border-radius: 50%;
    background: var(--green);
  }
  .divider {
    position: absolute; left: 268px; top: 100px;
    width: 2px; height: 104px; background: var(--green);
  }
  .person {
    position: absolute; left: 286px; top: 96px;
  }
  .person__name {
    font-weight: 700; font-size: 21px; color: var(--navy); line-height: 1.1;
  }
  .person__role {
    font-size: 12px; color: var(--ink); margin-top: 3px;
  }
  .contact { list-style: none; margin-top: 12px; }
  .contact__item {
    display: flex; align-items: center; gap: 6px;
    font-size: 11px; color: var(--ink); line-height: 1.6;
  }
  .contact__icon { width: 11px; height: 11px; flex: none; }
  .pillars {
    position: absolute; left: 200px; top: 230px;
    font-weight: 700; font-size: 15px;
  }
  .pillars__strategy { color: var(--cyan); }
  .pillars__execution { color: var(--green); }
  .pillars__results { color: var(--navy); }
  .footer-band { position: absolute; left: 0; bottom: 0; width: 540px; height: 44px; }
  .claim {
    position: absolute; right: 28px; bottom: 11px;
    font-size: 13px; color: #fff; letter-spacing: 0.3px;
  }
  /* Back */
  .card--back {
    background: var(--navy);
    display: flex; align-items: center; justify-content: center; gap: 12px;
  }
  .card--back .brand__name { color: var(--cream); font-size: 54px; }
  .card--back .brand__dot { width: 18px; height: 18px; }
</style>
</head>
<body>
<main class="sheet">
  <section class="card card--front" aria-label="Business card front">
    <div class="brand">
      <span class="brand__name">BrivoTerna</span>
      <span class="brand__dot"></span>
    </div>
    <div class="divider"></div>
    <div class="person">
      <p class="person__name">Teodoro Vinsquel</p>
      <p class="person__role">CEO &amp; Founder</p>
      <ul class="contact">
        <li class="contact__item">
          <svg class="contact__icon" viewBox="0 0 12 12"><rect x="2.5" y="0.8" width="7" height="10.4" rx="1.3" fill="none" stroke="var(--cyan)" stroke-width="1.2"/><circle cx="6" cy="9.4" r="0.7" fill="var(--cyan)"/></svg>
          +34 655.803.912
        </li>
        <li class="contact__item">
          <svg class="contact__icon" viewBox="0 0 12 12"><rect x="0.6" y="2.2" width="10.8" height="7.6" fill="var(--cyan)"/><path d="M0.6 2.2 L6 6.6 L11.4 2.2" fill="none" stroke="#fff" stroke-width="1"/></svg>
          teodoro.vinsquel@brivoterna-example.com
        </li>
        <li class="contact__item">
          <svg class="contact__icon" viewBox="0 0 12 12"><circle cx="6" cy="6" r="5.2" fill="none" stroke="var(--cyan)" stroke-width="1.1"/><ellipse cx="6" cy="6" rx="2.3" ry="5.2" fill="none" stroke="var(--cyan)" stroke-width="0.9"/><path d="M0.8 6 H11.2" stroke="var(--cyan)" stroke-width="0.9"/></svg>
          www.brivoterna-example.com
        </li>
      </ul>
    </div>
    <p class="pillars">
      <span class="pillars__strategy">Strategy,</span>
      <span class="pillars__execution">Execution,</span>
      <span class="pillars__results">Results</span>
    </p>
    <svg class="footer-band" viewBox="0 0 540 44" aria-hidden="true">
      <polygon points="0,30 250,30 240,44 0,44" fill="var(--green)"/>
      <polygon points="232,8 540,8 540,44 214,44" fill="var(--navy)"/>
    </svg>
    <p class="claim">Lantern of the Steady Harvest</p>
  </section>

  <section class="card card--back" aria-label="Business card back">
    <span class="brand__name">BrivoTerna</span>
    <span class="brand__dot"></span>
  </section>
</main>
</body>
</html>
```